Flyer / Small Safety "Poster" (A4 or 8.5x11" paper)

We're looking to create a series of safety signs for woodworkers to print on home printers using standard sized paper (A4 or 8.5x11" depending on where they are), or possibly to have printed on 17x22" paper.
Currently we want only the first one, but keep in mind that all should work together.
They need: Simple graphic. Bold Text. Company logo. Use company colors (orange, black, white.)
To begin, we will start with a single sign for hearing protection. Graphic or clip art to portray either ear plugs or ear-muff design. Text to say, "Hearing Protection is a Sound Investment."

Target Market(s)

USA Woodworkers & CNC Machinists - Male, 20-65 years old

Font styles to use
Sans Serif

Colors
f37122

Requirements
Must have
• Client logo
Nice to have
• Use client colors of black, white, & orange

```html
<!DOCTYPE html>
<html lang="en">
<head>
<meta charset="utf-8">
<title>Hearing Protection Is a Sound Investment – Bitline Supply Safety Sign</title>
<link rel="stylesheet" href="https://fonts.googleapis.com/css2?family=Anton&family=Montserrat:ital,wght@0,700;0,800;1,500&display=swap">
<style>
  :root {
    --orange: #f37122;
    --black: #111111;
    --white: #ffffff;
    --paper: #f4f4f4;
    --muff-light: #f8c98a;
    --slogan-grey: #333333;
  }
  * { margin: 0; padding: 0; box-sizing: border-box; }
  html, body { width: 800px; height: 1200px; overflow: hidden; background: var(--paper); }
  .sign {
    position: relative;
    width: 800px;
    height: 1200px;
    background: linear-gradient(160deg, var(--white) 0%, var(--paper) 100%);
    font-family: "Montserrat", Arial, sans-serif;
    color: var(--black);
  }
  .brand {
    position: absolute;
    top: 84px;
    left: 0;
    width: 100%;
    display: flex;
    justify-content: center;
    align-items: center;
    gap: 16px;
  }
  .brand-mark {
    width: 30px;
    height: 30px;
    background: var(--black);
  }
  .brand-name {
    font-family: "Montserrat", Arial, sans-serif;
    font-weight: 800;
    font-size: 54px;
    line-height: 0.98;
    letter-spacing: 2px;
    color: var(--black);
    text-transform: uppercase;
  }
  .slogan {
    position: absolute;
    top: 236px;
    width: 100%;
    text-align: center;
    font-style: italic;
    font-weight: 500;
    font-size: 20px;
    letter-spacing: -0.3px;
    color: var(--slogan-grey);
  }
  .earmuff-art {
    position: absolute;
    top: 322px;
    left: 36px;
    width: 724px;
    height: 725px;
    border-radius: 360px 360px 120px 120px;
    background: radial-gradient(ellipse at 50% 55%, #fff 30%, #fbe3cf 62%, var(--muff-light) 80%, #e9a06a 100%);
  }
  .headline {
    position: absolute;
    top: 470px;
    left: 190px;
    width: 420px;
    height: 450px;
  }
  .headline text { font-family: "Anton", Impact, sans-serif; }
  .headline .word-hearing { fill: var(--orange); }
  .headline .word-protection { fill: var(--black); }
  .subline {
    position: absolute;
    top: 800px;
    width: 100%;
    text-align: center;
    font-weight: 700;
    font-size: 56px;
    line-height: 1;
    color: var(--black);
  }
  .subline-accent {
    position: absolute;
    top: 868px;
    width: 100%;
    text-align: center;
    font-weight: 700;
    font-size: 43px;
    line-height: 1;
    letter-spacing: 0.5px;
    color: var(--orange);
  }
  .web {
    position: absolute;
    top: 1116px;
    width: 100%;
    text-align: center;
    font-weight: 700;
    font-size: 34px;
    letter-spacing: 1px;
    color: var(--black);
  }
  .web .domain { color: var(--orange); }
  .base-band {
    position: absolute;
    bottom: 0;
    left: 0;
    width: 100%;
    height: 8px;
    background: var(--orange);
  }
</style>
</head>
<body>
  <main class="sign">
    <header class="brand">
      <span class="brand-mark"></span>
      <span class="brand-name">Bitline<br>Supply</span>
    </header>
    <p class="slogan">Sharp bits for serious shop work!</p>

    <div class="earmuff-art" role="img" aria-label="Illustration of orange and dark grey safety earmuffs with a black headband, resting on a soft shadow"></div>

    <svg class="headline" viewBox="0 0 420 450" aria-label="Hearing Protection">
      <text class="word-hearing" x="4" y="196" font-size="230" textLength="404" lengthAdjust="spacingAndGlyphs">HEARING</text>
      <text class="word-protection" x="4" y="304" font-size="108" textLength="404" lengthAdjust="spacingAndGlyphs">PROTECTION</text>
    </svg>

    <p class="subline">Is a Sound</p>
    <p class="subline-accent">INVESTMENT</p>

    <p class="web">www.<span class="domain">bitlinesupply</span>.com</p>
    <div class="base-band"></div>
  </main>
</body>
</html>
```